Business Card Design - ChoiceCraft

Looking for creative, modern design, two sided for ChoiceCraft that is consistent with color and feel of website www.choicecraftpro.net.
Updates

Back of card will be used to promote products or have a quote revolving around decisions, change, leadership, innovation, creativity. Back should also have space to promote website, but optional to use the icon. Front of the card will need to use the icon and have standard place for name, job title, phone and email. We are not looking to put a mailing address or fax. Also want space to place a few words/phrase explaining what we do...such as individual growth and organizational development or tools, training, information...in addition, want the facebook icon small on the front somewhere as we are also on facebook.

Vector file uploaded of icon.

Target Market(s)

Professional coaching for individual growth and organizational development

Industry/Entity Type

Business

Requirements
Must have
• Icon...see attached.

```html
<!DOCTYPE html>
<html lang="en">
<head>
<meta charset="utf-8">
<title>ChoiceCraft Business Card</title>
<link href="https://fonts.googleapis.com/css2?family=Roboto:wght@400;700;900&display=swap" rel="stylesheet">
<style>
  :root {
    --page-bg: #e4e5e7;
    --card-bg: #ffffff;
    --ink: #222428;
    --ink-soft: #555a60;
    --brand-blue: #1f93d6;
    --brand-sky: #3fb0ea;
    --brand-navy: #23297a;
    --panel-grey: #c9ccd3;
    --quote-blue: #2a93d0;
  }
  * { box-sizing: border-box; margin: 0; padding: 0; }
  html, body { width: 1200px; height: 415px; overflow: hidden; }
  body {
    background: var(--page-bg);
    font-family: "Roboto", Arial, sans-serif;
    color: var(--ink);
    position: relative;
  }
  .card {
    position: absolute;
    width: 510px;
    height: 291px;
    background: var(--card-bg);
    box-shadow: 0 1px 3px rgba(0,0,0,.25);
    overflow: hidden;
  }
  .card-front { left: 75px; top: 55px; }
  .card-back { left: 613px; top: 58px; }

  /* front */
  .front-swoosh { position: absolute; inset: 0; }
  .brand-block {
    position: absolute; left: 20px; top: 30px; width: 210px;
    text-align: center;
  }
  .brand-mark {
    width: 110px; height: 110px; margin: 0 auto 24px;
    border-radius: 50%;
    background: radial-gradient(circle at 40% 35%, #e8f3fb 0%, var(--brand-sky) 55%, var(--brand-blue) 100%);
  }
  .brand-name { font-weight: 900; font-size: 22px; letter-spacing: .5px; color: var(--ink); }
  .holder { margin-top: 18px; font-size: 16px; font-weight: 700; color: var(--ink-soft); }
  .holder .title { font-weight: 400; font-size: 13px; }

  .contact-list {
    position: absolute; right: 14px; top: 76px;
    list-style: none; text-align: right; font-size: 13.5px; line-height: 20px; color: var(--ink);
  }
  .contact-list li { display: flex; justify-content: flex-end; align-items: center; gap: 5px; }
  .contact-list svg { width: 10px; height: 10px; flex: none; }
  .social-square { width: 8px; height: 8px; background: var(--ink-soft); display: inline-block; }
  .tagline {
    position: absolute; right: 14px; top: 176px;
    text-align: right; font-size: 12px; line-height: 15px; letter-spacing: .3px; color: var(--ink);
  }

  /* back */
  .quote-list { list-style: none; position: absolute; left: 27px; top: 24px; }
  .quote-item { display: flex; gap: 10px; height: 52px; }
  .quote-dot {
    width: 20px; height: 20px; margin-top: 4px; border-radius: 50%; flex: none;
    background: radial-gradient(circle at 40% 35%, #dcecf7, var(--brand-sky) 70%, var(--brand-blue));
  }
  .quote-text { font-size: 13.5px; line-height: 17px; color: var(--ink); }
  .mark { font-family: Georgia, serif; font-weight: 700; font-size: 20px; line-height: 0; }
  .mark-close { position: relative; top: 6px; }
  .quote-author { display: block; font-weight: 700; font-size: 13px; color: var(--quote-blue); margin-left: 12px; }
  .back-faint {
    position: absolute; left: 170px; top: 45px; width: 180px; height: 180px; border-radius: 50%;
    background: var(--brand-sky); opacity: .07;
  }
</style>
</head>
<body>
  <section class="card card-front">
    <svg class="front-swoosh" viewBox="0 0 510 291" width="510" height="291" aria-hidden="true">
      <defs>
        <radialGradient id="panelFade" cx="75%" cy="45%" r="70%">
          <stop offset="0" stop-color="#ffffff"/>
          <stop offset="0.55" stop-color="#eceef2"/>
          <stop offset="1" stop-color="var(--panel-grey)"/>
        </radialGradient>
      </defs>
      <path d="M292 0 Q175 150 325 291 L510 291 L510 0 Z" fill="var(--brand-sky)"/>
      <path d="M305 0 Q195 150 335 291 L510 291 L510 0 Z" fill="var(--brand-navy)"/>
      <path d="M322 0 Q215 150 345 291 L510 291 L510 0 Z" fill="#b8bcc6"/>
      <path d="M335 0 Q232 150 355 291 L510 291 L510 0 Z" fill="url(#panelFade)"/>
    </svg>

    <div class="brand-block">
      <div class="brand-mark"></div>
      <div class="brand-name">ChoiceCraft</div>
      <div class="holder">Your Name, <span class="title">Title</span></div>
    </div>

    <ul class="contact-list">
      <li><svg viewBox="0 0 10 10"><path d="M2 1 L4 1 L4.6 3.4 L3.4 4.2 Q4.4 6 5.8 6.6 L6.6 5.4 L9 6 L9 8 Q5 9.5 1 3 Z" fill="var(--ink)"/></svg>123-456-789</li>
      <li><svg viewBox="0 0 10 10"><rect x="0.5" y="2" width="9" height="6.5" fill="var(--ink)"/><path d="M0.5 2 L5 5.5 L9.5 2" stroke="#fff" fill="none"/></svg>info@choicecraftmail.com</li>
      <li><svg viewBox="0 0 10 10"><circle cx="5" cy="5" r="4.3" fill="none" stroke="var(--ink)"/><path d="M0.7 5 H9.3 M5 0.7 Q2 5 5 9.3 Q8 5 5 0.7" fill="none" stroke="var(--ink)" stroke-width=".8"/></svg>www.choicecraftpro.net</li>
      <li><span class="social-square"></span>/choicecraftpro</li>
    </ul>

    <p class="tagline">Supporting individual growth<br>and &nbsp;organizational development<br>or tools, training, information</p>
  </section>

  <section class="card card-back">
    <div class="back-faint"></div>
    <ul class="quote-list">
      <li class="quote-item"><span class="quote-dot"></span><p class="quote-text"><span class="mark">“</span> Try not to become a man of success, but rather a man of value.<span class="mark mark-close">”</span><span class="quote-author">- Alvin Ellery</span></p></li>
      <li class="quote-item"><span class="quote-dot"></span><p class="quote-text"><span class="mark">“</span> The only constant is change.<span class="mark mark-close">”</span><span class="quote-author">- Heron Tasos</span></p></li>
      <li class="quote-item"><span class="quote-dot"></span><p class="quote-text"><span class="mark">“</span> We are what we repeatedly do. Excellence is not an act, it is a habit.<span class="mark mark-close">”</span><span class="quote-author">- Aristo Melas</span></p></li>
      <li class="quote-item"><span class="quote-dot"></span><p class="quote-text"><span class="mark">“</span> Simplicity is the ultimate sophistication.<span class="mark mark-close">”</span><span class="quote-author">- Lorenzo DaVella</span></p></li>
      <li class="quote-item"><span class="quote-dot"></span><p class="quote-text"><span class="mark">“</span> Life is not fair - get used to it.<span class="mark mark-close">”</span><span class="quote-author">- Bill Garner</span></p></li>
    </ul>
  </section>
</body>
</html>
```